Business card for Luxury Portable Restroom Trailer company

We are a Luxury Portable Restroom Trailer Company Called FALCRIDGE HIRES. Based in Orange County California. We provide portable restroom trailers for events, such as, Weddings, Concerts, Charity events, Sporting events, Tournaments, Corporate events, ect. We rent and Sell the Luxury restrooms. Our colors are white, grey, and Orange. As you will see in the logo we uploaded.
There are 2 people in the company so the names and titles will change for the 3 people but card will remain the same. Here is the information for each Person: Dwight Penner CFO 555 318-0476
next Person: Leon Marchetti VP 555 318-0476
Next Person: Owen Marchetti CEO 555 318-0476
Information to include on the card: Luxury Restroom Trailers Rental and Sales. Weddings, Concerts, Charity, Sporting and Corp. Events.

```html
<!DOCTYPE html>
<html lang="en">
<head>
<meta charset="utf-8">
<title>Falcridge Hires – Business Card</title>
<link rel="stylesheet" href="https://fonts.googleapis.com/css2?family=Montserrat:wght@400;500;600;700;800&display=swap">
<style>
  :root {
    --orange: #e5692a;
    --grey-card: #58585a;
    --ink: #4a4a4c;
    --paper: #f6f6f4;
    --white: #f4f4f2;
    --stage: #1f1f20;
  }
  * { margin: 0; padding: 0; box-sizing: border-box; }
  html, body { width: 1200px; height: 1059px; overflow: hidden; }
  body {
    background: var(--stage);
    font-family: "Montserrat", sans-serif;
    position: relative;
  }
  .card {
    position: absolute;
    width: 688px;
    height: 392px;
    box-shadow: 0 10px 30px rgba(0,0,0,.55);
  }
  .card--front { left: 256px; top: 89px; background: var(--paper); color: var(--ink); }
  .card--back { left: 254px; top: 546px; background: var(--grey-card); color: var(--white); height: 394px; }

  .frame {
    position: absolute;
    left: 22px; right: 22px; top: 22px; bottom: 26px;
    border: 2px solid var(--orange);
    border-bottom: none;
  }
  .frame-base {
    position: absolute;
    left: 22px; right: 22px;
    display: flex; align-items: center; gap: 10px;
  }
  .frame-base::before, .frame-base::after {
    content: ""; flex: 1; height: 2px; background: var(--orange);
  }
  .card--front .frame-base { bottom: 25px; transform: translateY(50%); }
  .card--back .frame-base { bottom: 25px; transform: translateY(50%); }

  .wordmark {
    position: absolute; left: 0; right: 0;
    text-align: center;
    font-weight: 800;
    letter-spacing: 1px;
    line-height: 1;
  }
  .card--front .wordmark { top: 97px; font-size: 38px; color: var(--orange); }
  .card--back .wordmark { top: 168px; font-size: 46px; color: var(--white); }

  .person { position: absolute; left: 0; right: 0; top: 204px; text-align: center; }
  .person__name { font-size: 26px; font-weight: 700; color: var(--orange); letter-spacing: .5px; line-height: 1.15; }
  .person__title { font-size: 16px; font-weight: 400; margin-top: 4px; }
  .rule { width: 18px; height: 1px; background: var(--ink); margin: 0 auto; }
  .person .rule { margin-top: 11px; }

  .contacts {
    position: absolute; left: 0; right: 0; top: 279px;
    display: flex; justify-content: center; gap: 12px;
    font-size: 15.5px; white-space: nowrap;
  }
  .contacts li { list-style: none; display: flex; align-items: center; gap: 6px; }
  .contacts svg { width: 12px; height: 12px; fill: var(--orange); }
  .rule--lower { position: absolute; left: 335px; top: 312px; }

  .tagline {
    position: absolute; left: 0; right: 0; top: 329px;
    text-align: center; font-size: 16px; font-weight: 600; color: var(--orange);
  }
  .events { font-size: 16px; white-space: nowrap; }
  .url { font-size: 15px; letter-spacing: 2.2px; white-space: nowrap; }
</style>
</head>
<body>

<section class="card card--front">
  <div class="frame"></div>
  <div class="wordmark">FALCRIDGE HIRES</div>

  <div class="person">
    <div class="person__name">OWEN MARCHETTI</div>
    <div class="person__title">CEO</div>
    <div class="rule"></div>
  </div>

  <ul class="contacts">
    <li>
      <svg viewBox="0 0 24 24" aria-hidden="true"><path d="M6.6 10.8a15 15 0 0 0 6.6 6.6l2.2-2.2c.3-.3.7-.4 1-.2 1.1.4 2.3.6 3.6.6.6 0 1 .4 1 1V20c0 .6-.4 1-1 1A17 17 0 0 1 3 4c0-.6.4-1 1-1h3.5c.6 0 1 .4 1 1 0 1.3.2 2.5.6 3.6.1.3 0 .7-.2 1z"/></svg>
      555 318-0476
    </li>
    <li>
      <svg viewBox="0 0 24 24" aria-hidden="true"><path d="M2 9l10-6 10 6v11H2zM4 10v8h16v-8l-8 5z"/></svg>
      owen@falcridgehires.com
    </li>
    <li>
      <svg viewBox="0 0 24 24" aria-hidden="true"><circle cx="12" cy="12" r="10"/></svg>
      www.falcridgehires.com
    </li>
  </ul>
  <div class="rule rule--lower"></div>

  <div class="tagline">Luxury Restroom Trailers Rental and Sales</div>
  <div class="frame-base"><span class="events">Weddings I Concerts I Charity I Sporting I Corp</span></div>
</section>

<section class="card card--back">
  <div class="frame"></div>
  <div class="wordmark">FALCRIDGE HIRES</div>
  <div class="frame-base"><span class="url">www.falcridgehires.com</span></div>
</section>

</body>
</html>
```